BildeVOLD buisnesscard

Hey :) I need a modern buisnesscard for my company BildeVOLD
It most have:
Dagligleder og Fotograf: Henrik Audun Strandvik

Mob: +4791264085
Epost: post@bildevold.example
Adresse: Kvernbakken9, 6040 Fjordvik

Facbook and instagram logo with text BildeVOLD

BildeVOLD logo

It Company

```html
<!DOCTYPE html>
<html lang="no">
<head>
<meta charset="utf-8">
<title>BildeVOLD – visittkort</title>
<link rel="stylesheet" href="https://fonts.googleapis.com/css2?family=Noto+Sans:wght@400;600&display=swap">
<style>
  :root {
    --backdrop: #e4e4e4;
    --card: #252525;
    --ink: #a8a8a8;
    --shadow: rgba(0, 0, 0, 0.35);
  }
  * { margin: 0; padding: 0; box-sizing: border-box; }
  html, body {
    width: 1200px;
    height: 1200px;
    overflow: hidden;
    background: var(--backdrop);
    font-family: "Noto Sans", Verdana, sans-serif;
    color: var(--ink);
  }
  .card {
    position: absolute;
    width: 722px;
    height: 434px;
    background: var(--card);
    box-shadow: 0 4px 10px var(--shadow);
  }
  .card--front { left: 240px; top: 106px; }
  .card--back  { left: 238px; top: 624px; }

  .wordmark {
    position: absolute;
    right: 38px;
    top: 132px;
    font-size: 40px;
    font-weight: 600;
    letter-spacing: 0.5px;
    line-height: 1;
  }
  .holder { position: absolute; left: 44px; top: 200px; }
  .holder__name { font-size: 25px; font-weight: 400; letter-spacing: 0.6px; line-height: 1.2; }
  .holder__role { font-size: 16px; letter-spacing: 0.5px; margin-top: 4px; }

  .contact {
    position: absolute;
    left: 46px;
    top: 282px;
    list-style: none;
    font-size: 17px;
    letter-spacing: 0.5px;
  }
  .contact li { height: 30px; line-height: 24px; }
  .contact .contact__address { margin-top: 7px; }

  .back-mark {
    position: absolute;
    left: 0; right: 0;
    top: 200px;
    text-align: center;
    font-size: 60px;
    font-weight: 600;
    letter-spacing: 1px;
    line-height: 1;
  }
  .social {
    position: absolute;
    left: 0; right: 0;
    top: 334px;
    display: flex;
    justify-content: center;
    gap: 22px;
    font-size: 19px;
    letter-spacing: 0.6px;
  }
  .social__item { display: flex; align-items: center; gap: 10px; }
  .social__dot {
    width: 32px; height: 32px;
    border: 2px solid var(--ink);
    border-radius: 50%;
  }
</style>
</head>
<body>
  <section class="card card--front">
    <div class="wordmark">BildeVOLD</div>
    <div class="holder">
      <h1 class="holder__name">Henrik Audun Strandvik</h1>
      <p class="holder__role">Dagligleder og Fotograf</p>
    </div>
    <ul class="contact">
      <li>M: 912 640 85</li>
      <li>www.bildevold.example</li>
      <li>post@bildevold.example</li>
      <li class="contact__address">Kvernbakken9, 6040 Fjordvik</li>
    </ul>
  </section>

  <section class="card card--back">
    <div class="back-mark">BildeVOLD</div>
    <div class="social">
      <span class="social__item"><span class="social__dot"></span>BildeVOLD</span>
      <span class="social__item"><span class="social__dot"></span>BildeVOLD</span>
    </div>
  </section>
</body>
</html>
```